Venture 482 - Lumora Book Cover

I am looking for a Lumora book cover for my book about "Venture 482".
The Book is Titled:
Venture 482 Ascended
Shaping Outcomes: Paths To Unlocking Cosmic Truths
Author is Dorian Pell
Here is a book description that may help you understand more about it:
Inspired by the genius of Edwin Marlowe, this comprehensive guide delves into the ancient wisdom and cutting-edge science behind the 482 method, a powerful tool for manifesting your desires. Whether you're seeking personal growth, financial success, or spiritual enlightenment, this book provides advanced techniques and methods to transform your dreams into reality.
Any questions please ask.
Thanks
Owen

```html
<!DOCTYPE html>
<html lang="en">
<head>
<meta charset="utf-8">
<title>Venture 482 Ascended — Shaping Outcomes</title>
<link rel="stylesheet" href="https://fonts.googleapis.com/css2?family=Bebas+Neue&family=Oswald:wght@300;500&display=swap">
<style>
  :root {
    --page-bg: #ececec;
    --space-dark: #0a0a08;
    --gold-light: #fde38a;
    --gold-mid: #e9c46a;
    --gold-deep: #c9a24f;
    --text-white: #f4f2ee;
  }
  html, body {
    margin: 0;
    padding: 0;
    width: 1200px;
    height: 1200px;
    overflow: hidden;
    background: var(--page-bg);
  }
  .stage {
    position: relative;
    width: 1200px;
    height: 1200px;
  }
  .book-cover {
    position: absolute;
    left: 219px;
    top: 29px;
    width: 761px;
    height: 1142px;
    overflow: hidden;
    background: var(--space-dark);
  }
  .cosmic-artwork {
    position: absolute;
    inset: 0;
    background:
      radial-gradient(ellipse 22% 30% at 32% 22%, rgba(168,148,20,0.75), transparent 70%),
      radial-gradient(ellipse 25% 30% at 68% 25%, rgba(40,140,40,0.6), transparent 70%),
      radial-gradient(ellipse 28% 30% at 20% 55%, rgba(150,20,20,0.75), transparent 70%),
      radial-gradient(ellipse 28% 30% at 82% 55%, rgba(31,122,60,0.65), transparent 70%),
      radial-gradient(ellipse 20% 22% at 50% 52%, rgba(220,220,200,0.35), transparent 70%),
      radial-gradient(ellipse 24% 24% at 30% 76%, rgba(110,20,72,0.7), transparent 70%),
      radial-gradient(ellipse 16% 30% at 52% 82%, rgba(106,90,140,0.6), transparent 70%),
      radial-gradient(ellipse 22% 24% at 72% 88%, rgba(18,60,120,0.7), transparent 70%),
      linear-gradient(90deg, #1a0806 0%, #0a0a08 45%, #04140a 100%);
  }
  .cover-text {
    position: absolute;
    inset: 0;
    text-align: center;
  }
  .series-line {
    position: absolute;
    top: 246px;
    left: 0;
    right: 0;
    margin: 0;
    font-family: "Oswald", sans-serif;
    font-weight: 500;
    font-size: 34px;
    line-height: 52px;
    letter-spacing: 4px;
    color: var(--text-white);
  }
  .series-line .series-number {
    font-style: italic;
  }
  .book-title {
    position: absolute;
    top: 310px;
    left: 0;
    right: 0;
    margin: 0;
    font-family: "Bebas Neue", sans-serif;
    font-weight: 400;
    font-size: 192px;
    line-height: 152px;
    letter-spacing: 1px;
    background: linear-gradient(100deg, var(--gold-deep) 10%, var(--gold-mid) 35%, var(--gold-light) 50%, var(--gold-mid) 65%, var(--gold-deep) 90%);
    -webkit-background-clip: text;
    background-clip: text;
    color: transparent;
  }
  .book-title span {
    display: block;
  }
  .book-subtitle {
    position: absolute;
    top: 622px;
    left: 0;
    right: 0;
    margin: 0;
    font-family: "Oswald", sans-serif;
    font-weight: 300;
    font-size: 37px;
    line-height: 44px;
    color: var(--text-white);
  }
  .book-subtitle span {
    display: block;
  }
  .author-name {
    position: absolute;
    top: 1026px;
    left: 0;
    right: 0;
    margin: 0;
    font-family: "Oswald", sans-serif;
    font-weight: 500;
    font-size: 33px;
    letter-spacing: 10px;
    padding-left: 10px;
    color: var(--text-white);
  }
</style>
</head>
<body>
  <div class="stage">
    <section class="book-cover">
      <div class="cosmic-artwork" role="img" aria-label="Starry nebula in red, gold, green, violet and blue with a glowing sacred-geometry wireframe"></div>
      <div class="cover-text">
        <p class="series-line">VENTURE <span class="series-number">482</span> ASCENDED</p>
        <h1 class="book-title"><span>SHAPING</span><span>OUTCOMES</span></h1>
        <p class="book-subtitle"><span>PATHS TO</span><span>UNLOCKING COSMIC</span><span>TRUTHS</span></p>
        <p class="author-name">DORIAN PELL</p>
      </div>
    </section>
  </div>
</body>
</html>
```